Zenqo - revolutionary mobile payment

The app is a P2P money trasfert, without the using of credit card or bank circuits it can transfer electronic money from one person to another consumers simply and immediatelly.
You can use the color you want, but the message we need to transert to consumer is simplicity, safety and coolness.
In attach the logo of the company and the wireframe of thre page of the app.
The goal is to design the page of the app with a clear, simple and intuitive graphic.
Updates

I have upgrade the brief with important information and detail, many thanks

Target Market(s)

all the people

Industry/Entity Type

Credit Card

Requirements
Must have
• You have to design one icon for each button in the first page, (shop is: where to shop)
in the second one a new intuitive image (instead of the hand) that let the user to understand that with a simple swipe he can process the payment
Nice to have
• You can include or esxclude what you want or belive can improve user experience of the app
Should not have
• too much color, too much button or information

```html
<!DOCTYPE html>
<html lang="it">
<head>
<meta charset="utf-8">
<title>Zenqo – Pay</title>
<link href="https://fonts.googleapis.com/css2?family=Questrial&family=Nunito:wght@700;800&display=swap" rel="stylesheet">
<style>
  :root {
    --canvas-bg: #c4c7cc;
    --status-bg: #0c0c0e;
    --header-blue: #3d5185;
    --header-blue-light: #6d80ad;
    --nav-dark: #2b4074;
    --content-top: #dcdde6;
    --content-bottom: #b7b6c4;
    --field-white: #f4f4f6;
    --amount-top: #a7a4ab;
    --amount-bottom: #c9c7cd;
    --key-blue: #243a6c;
    --key-blue-light: #33497c;
    --key-line: #5c6f99;
    --accent-orange: #e14f08;
    --ink: #111111;
    --white: #ffffff;
  }
  * { box-sizing: border-box; margin: 0; padding: 0; }
  html, body {
    width: 1200px; height: 1195px; overflow: hidden;
    background: var(--canvas-bg);
    font-family: "Questrial", sans-serif;
  }
  .app-screen {
    position: absolute; left: 300px; top: 65px;
    width: 600px; height: 1065px;
    display: flex; flex-direction: column;
    overflow: hidden;
    box-shadow: 0 10px 40px rgba(0,0,0,.18);
  }
  .status-bar {
    height: 38px; background: var(--status-bg); color: var(--white);
    display: flex; align-items: center; justify-content: space-between;
    padding: 0 14px; font-size: 19px;
  }
  .status-left, .status-right { display: flex; align-items: center; gap: 8px; width: 200px; }
  .status-right { justify-content: flex-end; }
  .status-time { font-weight: 700; }
  .signal { display: flex; gap: 3px; }
  .signal span { width: 8px; height: 8px; border-radius: 50%; background: var(--white); }
  .signal span.off { background: transparent; border: 1px solid var(--white); }
  .app-header {
    height: 70px;
    background: linear-gradient(100deg, var(--header-blue) 0%, var(--header-blue) 45%, var(--header-blue-light) 100%);
    display: flex; align-items: center; justify-content: space-between;
    padding: 0 22px;
  }
  .brand { display: flex; align-items: center; gap: 8px; color: var(--white); font-size: 28px; }
  .brand-dot { width: 24px; height: 24px; border-radius: 50%; background: var(--white); }
  .nav-bar {
    height: 74px; position: relative;
    background: linear-gradient(90deg, var(--header-blue) 0%, #56689a 60%, #8e9abb 100%);
    display: flex; align-items: center; justify-content: center;
  }
  .back-button {
    position: absolute; left: 0; top: 0; bottom: 0; width: 130px;
    background: var(--nav-dark); color: var(--white);
    display: flex; align-items: center; justify-content: center; gap: 6px;
    font-size: 24px;
  }
  .screen-title { display: flex; align-items: center; gap: 12px; color: var(--white); font-family: "Nunito", sans-serif; font-weight: 800; font-size: 38px; }
  .pay-form {
    height: 403px; position: relative;
    background: linear-gradient(180deg, var(--content-top) 0%, #c9c9d4 60%, var(--content-bottom) 100%);
    padding: 26px 34px 0;
  }
  .search-field {
    height: 50px; margin-left: 60px; background: var(--field-white);
    border: 1px solid #c9c9cf;
  }
  .recipient-field {
    margin-top: 22px; height: 58px; background: var(--field-white);
    display: flex; align-items: center; gap: 16px;
    border: 1px solid #c9c9cf;
  }
  .recipient-icon {
    width: 58px; height: 58px; background: var(--white); border-right: 1px solid #bbb;
    display: flex; align-items: center; justify-content: center;
  }
  .recipient-prefix { font-size: 22px; color: var(--ink); font-weight: 700; }
  .recipient-placeholder { font-size: 24px; color: #333; }
  .amount-row { margin-top: 26px; display: flex; align-items: center; gap: 18px; }
  .currency { font-family: "Nunito", sans-serif; font-weight: 800; font-size: 50px; color: var(--ink); width: 42px; }
  .amount-field {
    flex: 1; height: 110px;
    background: linear-gradient(180deg, var(--amount-top), var(--amount-bottom));
    display: flex; align-items: center; justify-content: flex-end; padding-right: 30px;
    font-family: "Nunito", sans-serif; font-weight: 800; font-size: 58px; letter-spacing: 4px; color: var(--ink);
  }
  .notes-select {
    position: absolute; left: 34px; bottom: 0; height: 40px; width: 260px;
    background: #4e6192; color: #dfe4f0; font-size: 17px;
    display: flex; align-items: center; justify-content: space-between; padding: 0 14px;
  }
  .keypad {
    flex: 1; display: grid;
    grid-template-columns: repeat(3, 1fr); grid-template-rows: repeat(4, 1fr);
    gap: 2px; background: var(--key-line);
  }
  .key {
    background: linear-gradient(160deg, var(--key-blue-light), var(--key-blue));
    color: var(--white); font-family: "Nunito", sans-serif; font-weight: 800; font-size: 46px;
    display: flex; align-items: center; justify-content: center;
  }
  .key-active { background: var(--accent-orange); }
</style>
</head>
<body>
<main class="app-screen">
  <div class="status-bar">
    <div class="status-left">
      <div class="signal"><span></span><span></span><span></span><span class="off"></span><span class="off"></span></div>
      <span>Orvano</span>
      <svg width="20" height="16" viewBox="0 0 20 16"><path d="M2 6a12 12 0 0 1 16 0M5 9a7.5 7.5 0 0 1 10 0M8 12a3 3 0 0 1 4 0" stroke="#fff" stroke-width="2" fill="none"/></svg>
    </div>
    <span class="status-time">4:21 PM</span>
    <div class="status-right">
      <span>22%</span>
      <svg width="36" height="16" viewBox="0 0 36 16"><rect x="1" y="1" width="30" height="14" rx="2" stroke="#fff" stroke-width="1.5" fill="none"/><rect x="3" y="3" width="7" height="10" fill="#fff"/><rect x="32" y="5" width="3" height="6" fill="#fff"/></svg>
    </div>
  </div>

  <header class="app-header">
    <svg class="settings-icon" width="36" height="36" viewBox="0 0 36 36" aria-label="Impostazioni">
      <circle cx="18" cy="18" r="11" fill="none" stroke="#111" stroke-width="6" stroke-dasharray="4.3 4.3"/>
      <circle cx="18" cy="18" r="8" fill="#111"/>
      <circle cx="18" cy="18" r="3.5" fill="#3d5185"/>
    </svg>
    <div class="brand"><span class="brand-dot"></span><span class="brand-name">Zenqo</span></div>
  </header>

  <nav class="nav-bar">
    <div class="back-button">
      <svg width="12" height="20" viewBox="0 0 12 20"><path d="M10 2 2 10l8 8" stroke="#fff" stroke-width="2" fill="none"/></svg>
      <span>Indietro</span>
    </div>
    <h1 class="screen-title">
      <svg width="42" height="36" viewBox="0 0 42 36" aria-label="Scorri per pagare">
        <path d="M4 18h28M24 10l8 8-8 8" stroke="#fff" stroke-width="4" fill="none" stroke-linecap="round" stroke-linejoin="round"/>
      </svg>
      <span>Pay</span>
    </h1>
  </nav>

  <section class="pay-form">
    <div class="search-field"></div>
    <div class="recipient-field">
      <div class="recipient-icon">
        <svg width="34" height="40" viewBox="0 0 34 40"><rect x="3" y="3" width="28" height="34" rx="4" fill="none" stroke="#111" stroke-width="3"/><rect x="8" y="8" width="18" height="22" fill="#111"/></svg>
      </div>
      <span class="recipient-prefix">+39</span>
      <span class="recipient-placeholder">Cellulare</span>
    </div>
    <div class="amount-row">
      <span class="currency">€</span>
      <div class="amount-field">851.33</div>
    </div>
    <div class="notes-select"><span>Inserisci note (opzionale)</span><span>▾</span></div>
  </section>

  <div class="keypad">
    <div class="key">1</div><div class="key">2</div><div class="key">3</div>
    <div class="key">4</div><div class="key">5</div><div class="key">6</div>
    <div class="key">7</div><div class="key key-active">8</div><div class="key">9</div>
    <div class="key">.</div><div class="key">0</div>
    <div class="key" aria-label="Cancella">
      <svg width="54" height="30" viewBox="0 0 54 30"><path d="M14 1h39v28H14L1 15z" fill="#fff"/><path d="M27 9l12 12M39 9 27 21" stroke="#243a6c" stroke-width="3.5"/></svg>
    </div>
  </div>
</main>
</body>
</html>
```